Northfield Builders Guild Business card

We are looking for a new business card design with photo included.
Our business is a nonprofit construction contractor membership organization. We offer business education, assist with business setup and licensing, provide safety training, and provide a member directory.
URL: www.builderslinkguild.org
Color code:
CMYK: 0 cyan, 42 magenta, 100 yellow, 0 black for Print.
Hexidecimal: #FF9900
RGB: R 255; G 153; B 0

```html
<!DOCTYPE html>
<html lang="en">
<head>
<meta charset="utf-8">
<title>Northfield Builders Guild – Business Card</title>
<link rel="stylesheet" href="https://fonts.googleapis.com/css2?family=Montserrat:wght@800&family=Arimo:wght@400&display=swap">
<style>
  :root {
    --stage: #262626;
    --card-dark: #0a0a0a;
    --card-light: #f1f1f1;
    --orange: #ff9900;
    --ink: #111111;
    --white: #ffffff;
  }
  * { margin: 0; padding: 0; box-sizing: border-box; }
  html, body { width: 1200px; height: 1015px; overflow: hidden; }
  body {
    background: var(--stage);
    position: relative;
    font-family: "Arimo", Arial, sans-serif;
  }
  .card {
    position: absolute;
    width: 560px;
    height: 320px;
    box-shadow: 0 10px 30px rgba(0,0,0,.5);
  }
  .card--front { left: 60px; top: 150px; background: var(--card-dark); }
  .card--back  { left: 580px; top: 545px; background: var(--card-light); color: var(--ink); }

  .brand-name {
    font-family: "Montserrat", Arial, sans-serif;
    font-weight: 800;
    text-transform: uppercase;
    line-height: 1;
    color: var(--orange);
  }
  .card--front .brand-name {
    position: absolute;
    left: 0; right: 0; top: 96px;
    text-align: center;
    font-size: 38px;
    letter-spacing: 1px;
  }
  .card--front .brand-name span { display: block; }
  .card--front .site {
    position: absolute;
    left: 0; right: 0; top: 238px;
    text-align: center;
    font-size: 17px;
    letter-spacing: 1.5px;
    color: var(--orange);
  }
  .site .site-prefix { color: var(--white); }

  .card--back .brand-name {
    position: absolute;
    left: 34px; top: 34px;
    font-size: 24px;
    color: var(--ink);
  }
  .person { position: absolute; left: 34px; top: 128px; }
  .person-name {
    font-family: "Montserrat", Arial, sans-serif;
    font-weight: 800;
    font-size: 22px;
    color: var(--orange);
    text-transform: uppercase;
  }
  .person-title {
    font-family: "Montserrat", Arial, sans-serif;
    font-weight: 800;
    font-size: 13px;
    text-transform: uppercase;
    margin-top: 2px;
  }
  .contacts { position: absolute; left: 34px; top: 196px; list-style: none; }
  .contacts li {
    display: flex; align-items: center; gap: 8px;
    font-size: 15px; height: 24px;
  }
  .contacts svg { width: 18px; height: 18px; flex: none; }
  .address {
    position: absolute; left: 320px; top: 142px;
    font-size: 15px; line-height: 1.3; font-style: normal;
  }
  .card--back .site-url {
    position: absolute; left: 320px; top: 222px;
    font-size: 14px; color: var(--orange);
  }
</style>
</head>
<body>
  <section class="card card--front" aria-label="Business card front">
    <h1 class="brand-name"><span>Northfield</span><span>Builders Guild</span></h1>
    <p class="site"><span class="site-prefix">www.</span>builderslinkguild.org</p>
  </section>

  <section class="card card--back" aria-label="Business card back">
    <p class="brand-name">Northfield Builders Guild</p>
    <div class="person">
      <p class="person-name">Daniel Marsh</p>
      <p class="person-title">Managing Director</p>
    </div>
    <ul class="contacts">
      <li>
        <svg viewBox="0 0 18 18" aria-hidden="true"><circle cx="9" cy="9" r="9" fill="#ff9900"/><path d="M6 4.5c.6 0 1.5 2 1.2 2.5l-.7.8c.5 1.3 1.4 2.2 2.7 2.7l.8-.7c.5-.3 2.5.6 2.5 1.2 0 1-1 1.7-1.8 1.5C7.9 12 6 10.1 5.5 7.3 5.3 5.5 5.1 4.5 6 4.5z" fill="#fff"/></svg>
        (555) 201-3384
      </li>
      <li>
        <svg viewBox="0 0 18 18" aria-hidden="true"><circle cx="9" cy="9" r="9" fill="#ff9900"/><rect x="6" y="4" width="6" height="10" rx="1" fill="none" stroke="#fff" stroke-width="1.4"/></svg>
        555-014-2270
      </li>
      <li>
        <svg viewBox="0 0 18 18" aria-hidden="true"><circle cx="9" cy="9" r="9" fill="#ff9900"/><rect x="6.5" y="4" width="5" height="3" fill="#fff"/><rect x="4.5" y="7.5" width="9" height="4" fill="#fff"/><rect x="6.5" y="11" width="5" height="3" fill="#fff"/></svg>
        555.302.7715
      </li>
      <li>
        <svg viewBox="0 0 18 18" aria-hidden="true"><circle cx="9" cy="9" r="9" fill="#ff9900"/><rect x="4.5" y="5.5" width="9" height="7" fill="#fff"/><path d="M4.5 5.5L9 9.5l4.5-4" fill="none" stroke="#ff9900" stroke-width="1"/></svg>
        support@nbguild.org
      </li>
    </ul>
    <address class="address">2400 Harbor Lane<br>Suite #210, Fairview<br>OR 97000</address>
    <p class="site-url">www.builderslinkguild.org</p>
  </section>
</body>
</html>
```